Create a wordpress website for Tovarin business solution

This project is to create a complete website with all pages.

Overview
The purpose of this project is to create a full complete website with all pages (16 pages). The site should be professional and modern. The site is for an IT recruiting and IT training company. The site needs to be easy to administer and update content. It should be simple to add pages, videos and testimonials later. I will leave the site layout, color schemes and flow to the designers.

Navigation Menu (Home, who we are, what we do, what makes us different, why it matters, candidate portal, contact us, Blog)

WHO WE ARE should be a drop down menu with link to pages (about us, mission, vision and purpose, our team)

WHAT WE DO should be drop down menu with link to the following pages (IT Recruiting, IT Training, Hardware and software sales)

What makes us different should be single page with different paragraph titles. (We live what we do, we don't compromise quality, we share knowledge, staffing guarantee)

Why it matters should be single page with paragraph titles. (Quickly fill positions, candidate career development)

Candidate portal should links to my portal login page. I can add the correct URL later. I just need it to link to somewhere. I can change it.

Contact us should have (address, phone number, Location Map and a form to submit request for a call back)

Blog - This link should launch a wordpress blogging module

Target Market(s)

IT RECRUITING AND CONSULTING

Industry/Entity Type

It Company

Coding

Coded - Design and coding required

Requirements
Must have
• Company Logo
• Navigation Menu (Home, who we are, what we do, what makes us different, why it matters, candidate portal, contact us)
• WHO WE ARE should be a drop down menu with link to pages (about us, mission, vision and purpose, our team)
• WHAT WE DO should be drop down menu with link to the following pages (IT Recruiting, IT Training, Hardware and software sales)
• What makes us different should be single page with different paragraph titles. (We live what we do, we don't compromise quality, we share knowledge, staffing guarantee)
• Why it matters should be single page with paragraph titles. (Quickly fill positions, candidate career development)
• Candidate portal should links to my portal login page. I can add the correct URL later. I just need it to link to somewhere. I can change it.
• Contact us should have (address, phone number, Location Map and a form to submit request for a call back)

```html
<!DOCTYPE html>
<html lang="en">
<head>
<meta charset="utf-8">
<title>Tovarin Business Solution</title>
<link href="https://fonts.googleapis.com/css2?family=Oswald:wght@500;600&family=Open+Sans:wght@400;600;700&display=swap" rel="stylesheet">
<style>
:root{
  --orange:#e8781d;
  --orange-light:#f7a35c;
  --orange-dark:#d5680f;
  --blue:#1b5ba3;
  --ink:#333;
  --muted:#777;
  --light:#f1f1f1;
  --footer:#1c1c1c;
  --white:#fff;
}
*{margin:0;padding:0;box-sizing:border-box}
html,body{width:1200px;height:4138px;overflow:hidden}
body{font-family:"Open Sans",Arial,sans-serif;color:var(--ink);background:var(--white);font-size:15px}
section,header,nav,footer{position:relative;width:1200px;overflow:hidden}
.abs{position:absolute}

/* header */
.top-bar{height:116px}
.brand{left:77px;top:14px;display:flex;flex-direction:column}
.brand-name{font-size:56px;font-weight:700;color:var(--blue);line-height:1;letter-spacing:1px}
.brand-tag{font-size:15px;color:var(--blue);letter-spacing:2px;margin-top:4px}
.call{right:82px;top:34px;display:flex;align-items:center;gap:14px;font-size:27px}
.call-label{color:var(--orange)}
.call-icon{width:52px;height:52px;border:3px solid var(--blue);border-radius:50%;display:flex;align-items:center;justify-content:center}
.call-number{color:var(--orange)}

.main-nav{height:63px;border-top:1px solid #e3e3e3;border-bottom:1px solid #e3e3e3}
.main-nav ul{list-style:none;display:flex;justify-content:space-between;position:absolute;left:77px;right:77px;top:0;height:63px;align-items:center}
.main-nav li{font-size:15px;font-weight:600;text-transform:uppercase;color:#444;padding:0 10px;height:63px;display:flex;align-items:center}
.main-nav li.active{background:var(--orange);color:var(--white);padding:0 14px}

/* hero */
.hero{height:497px}
.hero-photo{inset:0;background:linear-gradient(90deg,#6b7076 0%,#a7acb1 45%,#8a8f93 70%,#4e5256 100%)}
.hero-shade{inset:0;background:linear-gradient(90deg,rgba(0,0,0,.35),rgba(0,0,0,0) 60%)}
.hero h1{left:77px;top:128px;font-family:"Oswald",Arial,sans-serif;font-weight:600;font-size:64px;line-height:1.2;color:#1c1c1c}
.hero p{left:77px;top:224px;width:670px;font-size:16px;line-height:25px;color:var(--white)}
.btn-solid{background:var(--orange);color:var(--white);font-size:19px;text-transform:uppercase;display:flex;align-items:center;justify-content:center}
.hero .btn-solid{left:77px;top:312px;width:188px;height:56px}
.hero-arrow{left:28px;top:236px}

/* section heading */
.heading{left:0;right:0;text-align:center}
.heading h2{font-size:42px;font-weight:400;color:var(--blue);letter-spacing:1px;text-transform:uppercase;line-height:1.1}
.heading h2 span{color:var(--orange)}
.heading .sub{display:inline-flex;align-items:center;gap:16px;font-size:14px;color:#555;margin-top:10px}
.heading .sub::before,.heading .sub::after{content:"";width:130px;height:2px;background:var(--orange)}
.lead{left:160px;right:160px;text-align:center;font-size:14px;line-height:27px;color:#666}

/* welcome */
.welcome{height:607px}
.welcome .heading{top:44px}
.welcome .lead{top:148px}
.service{width:300px;text-align:center;top:229px}
.service .circle{width:186px;height:186px;border-radius:50%;background:var(--orange);margin:0 auto;box-shadow:0 0 0 6px #fbe0c8}
.service h3{font-size:19px;font-weight:400;color:var(--orange);margin-top:36px;text-transform:uppercase}
.service p{font-size:14px;line-height:24px;color:#888;margin-top:10px;padding:0 20px}

/* video */
.video{height:394px}
.video-photo{inset:0;background:linear-gradient(135deg,#2a2522 0%,#4a423c 50%,#1b1816 100%)}
.video h2{left:0;right:0;top:104px;text-align:center;color:var(--white);font-size:44px;font-weight:400;text-transform:uppercase;letter-spacing:1px}
.video h2 span{color:var(--orange)}
.play{left:550px;top:185px}

/* candidate */
.candidate{height:166px;background:var(--orange);color:var(--white)}
.candidate h2{left:77px;top:28px;font-size:33px;font-weight:400;text-transform:uppercase}
.candidate p{left:77px;top:84px;width:860px;font-size:14px;line-height:27px}
.btn-outline{border:2px solid var(--white);color:var(--white);font-size:19px;text-transform:uppercase;display:flex;align-items:center;justify-content:center}
.candidate .btn-outline{left:985px;top:58px;width:138px;height:58px}

/* blog */
.blog{height:557px}
.blog .heading{top:48px}
.post{top:166px;width:331px;text-align:center}
.post-photo{height:190px;background:linear-gradient(135deg,#c9b8a4,#8f7f6f)}
.post-photo.light{background:linear-gradient(135deg,#e6e3df,#b9b2aa)}
.post-photo.cool{background:linear-gradient(135deg,#9aa3ad,#56606b)}
.post .plus{position:absolute;left:142px;top:164px;width:48px;height:48px;border-radius:50%;background:var(--orange);border:3px solid var(--white)}
.post h3{font-size:21px;font-weight:400;color:#222;margin-top:50px}
.post p{font-size:14px;line-height:24px;color:#888;margin-top:8px;padding:0 10px}

/* different / matters */
.values{height:420px;background:var(--light)}
.values .divider{left:580px;top:0;width:10px;height:420px;background:linear-gradient(90deg,rgba(0,0,0,.08),rgba(0,0,0,0))}
.col{top:52px;width:505px}
.col h2{font-size:32px;font-weight:400;color:var(--blue);text-transform:uppercase}
.col h2 span{color:var(--orange)}
.col p{font-size:14px;line-height:24px;color:#666;margin-top:16px}
.col ul{list-style:none;margin-top:14px}
.col li{font-size:14px;color:#444;padding-left:30px;position:relative;margin-top:12px}
.col li::before{content:"";position:absolute;left:0;top:9px;width:18px;height:2px;background:var(--orange)}
.col li.open{color:var(--orange);font-size:16px;margin-left:30px}
.col li.open p{color:#666;font-size:14px;margin-top:8px}

/* testimonial */
.testimonial{height:444px}
.testimonial .heading{top:63px}
.avatar{left:552px;top:174px;width:96px;height:96px;border-radius:50%;border:4px solid #eee;background:linear-gradient(160deg,#d9c1ad,#6b4a38)}
.quote{left:160px;right:160px;top:298px;text-align:center;font-size:14px;line-height:27px;color:#555}
.qmark{color:var(--orange);font-family:Georgia,serif;font-size:40px;line-height:0;vertical-align:-10px}
.client{left:0;right:0;top:360px;text-align:center;font-size:15px;color:var(--orange);text-transform:uppercase}
.client::before{content:"";display:inline-block;width:26px;height:2px;background:var(--orange);vertical-align:middle;margin-right:14px}

/* contact */
.contact{height:521px;background:var(--orange)}
.contact .heading{top:48px}
.contact .heading h2 span{color:var(--orange-light)}
.contact .heading .sub{color:var(--white)}
.contact .heading .sub::before,.contact .heading .sub::after{background:var(--white)}
.contact .lead{top:152px;color:var(--white)}
.field{border:2px solid rgba(255,255,255,.75);color:var(--white);font-size:14px;padding:12px}
.contact .btn-outline{left:524px;top:403px;width:152px;height:56px}

/* footer */
.site-footer{height:353px;background:var(--footer);color:#bbb}
.footer-photo{inset:0;background:linear-gradient(180deg,#2a2a2a 0%,#151515 100%)}
.fcol{top:30px;width:240px}
.fcol h4{font-size:16px;font-weight:600;color:var(--orange);text-transform:uppercase;margin-bottom:14px}
.fcol li{list-style:none;font-size:13px;line-height:27px;color:#ccc}
.info{display:flex;gap:12px;font-size:13px;line-height:21px;margin-bottom:10px}
.info .ic{flex:0 0 22px}
.info .hi{color:var(--orange)}
.socials{display:flex;gap:12px;margin-top:8px}
.socials span{width:38px;height:38px;border-radius:50%;background:var(--orange)}
.map{width:240px;height:150px;background:linear-gradient(135deg,#e9e6df,#cfd8cf)}
.map-cap{font-size:13px;color:#ccc;margin-top:10px;text-align:center}
.fcol .note{font-size:13px;line-height:21px;color:#ccc;margin-bottom:14px}
.email{background:var(--white);color:#888;font-size:13px;padding:10px;height:40px}
.subscribe{margin-top:14px;width:158px;height:42px;background:var(--orange);color:var(--white);font-size:16px;text-transform:uppercase;display:flex;align-items:center;justify-content:center}
.copyright{left:0;right:0;bottom:0;height:36px;text-align:center;font-size:13px;line-height:36px;color:#ccc;border-top:1px solid #333}
.copyright span{color:var(--orange)}
</style>
</head>
<body>

<header class="top-bar">
  <div class="brand abs">
    <span class="brand-name">Tovarin</span>
    <span class="brand-tag">BUSINESS SOLUTION LLC</span>
  </div>
  <div class="call abs">
    <span class="call-label">Call Us :</span>
    <span class="call-icon">
      <svg width="24" height="24" viewBox="0 0 24 24"><path d="M6.6 10.8a15 15 0 0 0 6.6 6.6l2.2-2.2c.3-.3.7-.4 1-.2 1.1.4 2.3.6 3.6.6.6 0 1 .4 1 1V20c0 .6-.4 1-1 1A17 17 0 0 1 3 4c0-.6.4-1 1-1h3.5c.6 0 1 .4 1 1 0 1.3.2 2.5.6 3.6.1.3 0 .7-.2 1z" fill="#1b5ba3"/></svg>
    </span>
    <span class="call-number">555 010 2040</span>
  </div>
</header>

<nav class="main-nav">
  <ul>
    <li class="active">Home</li>
    <li>Who We Are</li>
    <li>What We Do</li>
    <li>What Makes Us Different</li>
    <li>Why It Matters</li>
    <li>Candidate Portal</li>
    <li>Contact Us</li>
  </ul>
</nav>

<section class="hero">
  <div class="hero-photo abs" role="img" aria-label="Two smiling colleagues planning at a whiteboard in a bright office"></div>
  <div class="hero-shade abs"></div>
  <svg class="hero-arrow abs" width="16" height="28" viewBox="0 0 16 28"><path d="M13 2 3 14l10 12" stroke="#fff" stroke-width="2.5" fill="none"/></svg>
  <h1 class="abs">BUSINESS SOLUTION</h1>
  <p class="abs">Lorem Ipsum is simply dummy text of the printing and typesetting industry Lorem Ipsum has been the industry's standard dummy text ever since the 1500s, when an unknown printer took a galley of type and scrambled it to.</p>
  <div class="btn-solid abs">Contact Us</div>
</section>

<section class="welcome">
  <div class="heading abs">
    <h2>Welcome to <span>Tovarin</span></h2>
    <div class="sub">Business Solution LLC</div>
  </div>
  <p class="lead abs">Lorem Ipsum is simply dummy text of the printing and typesetting industry. Lorem Ipsum has been the industry's standard dummy text ever since the 1500s, when an unknown printer took a galley of type and scrambled it to make a type specimen book.</p>

  <div class="service abs" style="left:98px">
    <div class="circle" role="img" aria-label="Illustration of a recruiting meeting"></div>
    <h3>IT Recruiting</h3>
    <p>Lorem Ipsum is simply dummy text of the printing and typesetting industry Lorem Ipsum has been the industry's .</p>
  </div>
  <div class="service abs" style="left:451px">
    <div class="circle" role="img" aria-label="Illustration of a training class"></div>
    <h3>IT Training</h3>
    <p>Lorem Ipsum is simply dummy text of the printing and typesetting industry Lorem Ipsum has been the industry's .</p>
  </div>
  <div class="service abs" style="left:805px">
    <div class="circle" role="img" aria-label="Illustration of computer hardware and software"></div>
    <h3>Hardware &amp; Software Sales</h3>
    <p>Lorem Ipsum is simply dummy text of the printing and typesetting industry Lorem Ipsum has been the industry's .</p>
  </div>
</section>

<section class="video">
  <div class="video-photo abs" role="img" aria-label="Hands typing on a laptop keyboard in low light"></div>
  <h2 class="abs">Watch <span>a Video</span></h2>
  <svg class="play abs" width="100" height="100" viewBox="0 0 100 100"><circle cx="50" cy="50" r="46" stroke="#e8781d" stroke-width="5" fill="rgba(0,0,0,.15)"/><path d="M40 30v40l32-20z" fill="#e8781d"/></svg>
</section>

<section class="candidate">
  <h2 class="abs">Candidate Portal</h2>
  <p class="abs">Lorem Ipsum is simply dummy text of the printing and typesetting industry. Lorem Ipsum has been the industry's standard dummy text ever since the 1500s, when an unknown printer took a galley of type and scrambled it to make a type specimen book.</p>
  <div class="btn-outline abs">Login</div>
</section>

<section class="blog">
  <div class="heading abs">
    <h2>Latest <span>Blog</span></h2>
    <div class="sub">New Update</div>
  </div>
  <article class="post abs" style="left:77px">
    <div class="post-photo" role="img" aria-label="Business team meeting around a desk"></div>
    <span class="plus"><svg width="42" height="42" viewBox="0 0 42 42"><path d="M21 12v18M12 21h18" stroke="#fff" stroke-width="3"/></svg></span>
    <h3>Lorem Ipsum is simply dummy</h3>
    <p>Lorem Ipsum is simply dummy text of the printing and typesetting industry. Lorem Ipsum has been the industry's..</p>
  </article>
  <article class="post abs" style="left:433px">
    <div class="post-photo light" role="img" aria-label="Young professionals working together in a bright room"></div>
    <span class="plus"><svg width="42" height="42" viewBox="0 0 42 42"><path d="M21 12v18M12 21h18" stroke="#fff" stroke-width="3"/></svg></span>
    <h3>Lorem Ipsum is simply dummy</h3>
    <p>Lorem Ipsum is simply dummy text of the printing and typesetting industry. Lorem Ipsum has been the industry's..</p>
  </article>
  <article class="post abs" style="left:789px">
    <div class="post-photo cool" role="img" aria-label="Businessman in a suit writing at a desk"></div>
    <span class="plus"><svg width="42" height="42" viewBox="0 0 42 42"><path d="M21 12v18M12 21h18" stroke="#fff" stroke-width="3"/></svg></span>
    <h3>Lorem Ipsum is simply dummy</h3>
    <p>Lorem Ipsum is simply dummy text of the printing and typesetting industry. Lorem Ipsum has been the industry's..</p>
  </article>
</section>

<section class="values">
  <div class="divider abs"></div>
  <div class="col abs" style="left:77px">
    <h2>What Makes <span>Us Different</span></h2>
    <p>Lorem Ipsum is simply dummy text of the printing and typesetting industry. Lorem Ipsum has been the industry's standard.</p>
    <ul>
      <li class="open">What We Do ?<p>Lorem Ipsum is simply dummy text of the printing and typesetting industry. Lorem Ipsum has been the industry's standard.</p></li>
      <li>We don't Compromise Quality</li>
      <li>We Share Knowledge</li>
      <li>Staffing Guarantee</li>
    </ul>
  </div>
  <div class="col abs" style="left:627px">
    <h2>Why It <span>Matters</span></h2>
    <p>Lorem Ipsum is simply dummy text of the printing and typesetting industry. Lorem Ipsum has been the industry's standard.</p>
    <ul>
      <li class="open" style="margin-left:0">Quickly Fill Positions<p>Lorem Ipsum is simply dummy text of the printing and typesetting industry. Lorem Ipsum has been the industry's standard.</p></li>
      <li>Candidate Career Development</li>
    </ul>
  </div>
</section>

<section class="testimonial">
  <div class="heading abs">
    <h2>Testimonial</h2>
    <div class="sub">What They Say</div>
  </div>
  <div class="avatar abs" role="img" aria-label="Client portrait"></div>
  <p class="quote abs"><span class="qmark">&ldquo;</span> Lorem Ipsum is simply dummy text of the printing and typesetting industry. Lorem Ipsum has been the industry's standard dummy text ever since the 1500s, when an unknown printer took a galley of type and scrambled it to make a <span class="qmark">&rdquo;</span></p>
  <div class="client abs">Client Name</div>
</section>

<section class="contact">
  <div class="heading abs">
    <h2>Contact <span>Us</span></h2>
    <div class="sub">New Update</div>
  </div>
  <p class="lead abs">Lorem Ipsum is simply dummy text of the printing and typesetting industry. Lorem Ipsum has been the industry's standard dummy text ever since the 1500s, when an unknown printer took a galley of type and</p>
  <div class="field abs" style="left:152px;top:218px;width:292px;height:52px">Name*</div>
  <div class="field abs" style="left:458px;top:218px;width:288px;height:52px">Email*</div>
  <div class="field abs" style="left:756px;top:218px;width:290px;height:52px">Phone*</div>
  <div class="field abs" style="left:152px;top:280px;width:894px;height:114px">Message*</div>
  <div class="btn-outline abs">Submit</div>
</section>

<footer class="site-footer">
  <div class="footer-photo abs" role="img" aria-label="Faded silhouettes of a business crowd"></div>
  <div class="fcol abs" style="left:77px">
    <h4>Sitemap</h4>
    <ul>
      <li style="color:var(--orange)">» Home</li>
      <li>» Who We Are</li>
      <li>» What We Do</li>
      <li>» What Makes Us Different</li>
      <li>» Why It Matters</li>
      <li>» Candidate Portal</li>
      <li>» Contact Us</li>
    </ul>
  </div>
  <div class="fcol abs" style="left:339px">
    <h4>Get In Touch</h4>
    <div class="info"><svg class="ic" width="22" height="26" viewBox="0 0 22 26"><path d="M11 1a9 9 0 0 0-9 9c0 7 9 15 9 15s9-8 9-15a9 9 0 0 0-9-9z" fill="none" stroke="#e8781d" stroke-width="2"/><circle cx="11" cy="10" r="3" fill="#e8781d"/></svg><div><span class="hi">Tovarin Business Solution LLC</span><br>105 - Lorem Ipsum is simple dummy text of print.</div></div>
    <div class="info"><svg class="ic" width="22" height="22" viewBox="0 0 24 24"><path d="M6.6 10.8a15 15 0 0 0 6.6 6.6l2.2-2.2c.3-.3.7-.4 1-.2 1.1.4 2.3.6 3.6.6.6 0 1 .4 1 1V20c0 .6-.4 1-1 1A17 17 0 0 1 3 4c0-.6.4-1 1-1h3.5c.6 0 1 .4 1 1 0 1.3.2 2.5.6 3.6.1.3 0 .7-.2 1z" fill="#e8781d"/></svg><div>+555 010 2040</div></div>
    <div class="info"><svg class="ic" width="22" height="18" viewBox="0 0 22 18"><rect x="1" y="2" width="20" height="14" fill="none" stroke="#e8781d" stroke-width="2"/><path d="m1 3 10 7 10-7" fill="none" stroke="#e8781d" stroke-width="2"/></svg><div>info@tovarin.com</div></div>
    <div class="socials"><span></span><span></span><span></span></div>
  </div>
  <div class="fcol abs" style="left:610px">
    <h4>Location Map</h4>
    <div class="map" role="img" aria-label="Street map showing the office location"></div>
    <div class="map-cap">Tovarin Business Solution LLC</div>
  </div>
  <div class="fcol abs" style="left:872px;width:250px">
    <h4>Newsletter</h4>
    <p class="note">Would you like to receive exclusive access to articles, white papers and our regular monthly newsletter?</p>
    <div class="email">Enter Email Id</div>
    <div class="subscribe">Subscribe</div>
  </div>
  <div class="copyright abs">©<span>Tovarin Business Solution LLC</span> - 2016. All Rights Reserved</div>
</footer>

</body>
</html>
```